Company identity deisgn should support 2 languages

I would like to get our company identity design
This includes the following only
Business Cards 2 languages Arabic and English
Email signature
Letterhead
Linkedin profile images
Attached is the logo in Ai format

Requirements
Must have
• For business card
Must have
Name and Adrees in arabic
Name and Address in english
You might use both side of the card
Should not have
• Any pictures other than the logo

```html
<!DOCTYPE html>
<html lang="en">
<head>
<meta charset="utf-8">
<title>Novaline Systems — Business Cards</title>
<link rel="stylesheet" href="https://fonts.googleapis.com/css2?family=Montserrat:wght@400;500;700&family=Cairo:wght@400;600;700&display=swap">
<style>
  :root {
    --brand-blue: #0f76bd;
    --edge-grey: #bcbcbc;
    --paper: #ffffff;
    --backdrop: #e6e6e6;
    --ink-light: #ffffff;
  }
  * { margin: 0; padding: 0; box-sizing: border-box; }
  html, body { width: 1200px; height: 1200px; overflow: hidden; }
  body { background: var(--backdrop); position: relative; font-family: "Montserrat", sans-serif; }

  .card {
    position: absolute; left: 262px; width: 686px; height: 392px;
    border-radius: 26px; overflow: hidden; background: var(--paper);
  }
  .card--english { top: 165px; }
  .card--arabic { top: 653px; }
  .card__shape { position: absolute; inset: 0; width: 100%; height: 100%; }

  .card__details { position: absolute; color: var(--ink-light); }
  .card--english .card__details { left: 28px; top: 90px; }
  .card--arabic .card__details { left: 21px; top: 90px; }

  .person__name { font-weight: 700; font-size: 22px; letter-spacing: 0.2px; line-height: 1.2; }
  .person__role { font-size: 15px; font-weight: 400; margin-top: 2px; }
  .address { font-size: 15px; line-height: 20px; margin-top: 15px; }
  .contact-list { list-style: none; margin-top: 15px; font-size: 15px; line-height: 19.4px; }
  .contact-list li { display: flex; align-items: center; gap: 9px; }
  .contact-list svg { width: 13px; height: 13px; fill: var(--ink-light); flex: none; }

  .arabic { font-family: "Cairo", sans-serif; direction: rtl; text-align: left; }
  .card--arabic .person__name { font-family: "Cairo", sans-serif; font-weight: 700; font-size: 23px; line-height: 1.1; }
  .card--arabic .person__role { font-family: "Cairo", sans-serif; font-size: 17px; line-height: 1.1; margin-top: 0; }
  .card--arabic .address { font-size: 14px; line-height: 23px; margin-top: 8px; }
  .card--arabic .contact-list { margin-top: 8px; }

  .brand { position: absolute; display: flex; align-items: center; gap: 10px; }
  .card--english .brand { left: 352px; top: 180px; }
  .card--arabic .brand { left: 328px; top: 180px; }
  .brand__dot { width: 30px; height: 30px; border-radius: 50%; background: var(--brand-blue); flex: none; }
  .brand__name { font-family: "Montserrat", sans-serif; font-weight: 500; font-size: 21px; color: var(--brand-blue); letter-spacing: 0.5px; }
</style>
</head>
<body>

<svg width="0" height="0" style="position:absolute" aria-hidden="true">
  <defs>
    <symbol id="icon-phone" viewBox="0 0 16 16"><path d="M3.6 1 6 1.4l1 3.4-1.6 1.3a9 9 0 0 0 4.5 4.5l1.3-1.6 3.4 1V12.4C14.6 14 13.6 15 12 15 6.5 15 1 9.5 1 4 1 2.4 2 1.4 3.6 1z"/></symbol>
    <symbol id="icon-mobile" viewBox="0 0 16 16"><path d="M4 0h8a1 1 0 0 1 1 1v14a1 1 0 0 1-1 1H4a1 1 0 0 1-1-1V1a1 1 0 0 1 1-1zm1 2v10h6V2zm3 11a1 1 0 1 0 0 2 1 1 0 0 0 0-2z"/></symbol>
    <symbol id="icon-fax" viewBox="0 0 16 16"><path d="M4 1h8v4H4zM1 6h14v6h-2v3H3v-3H1zm4 5v2h6v-2z"/></symbol>
    <symbol id="icon-mail" viewBox="0 0 16 16"><path d="M1 3h14v10H1zm1.5 1.2L8 8.6l5.5-4.4z"/></symbol>
    <symbol id="icon-globe" viewBox="0 0 16 16"><path d="M8 1a7 7 0 1 0 0 14A7 7 0 0 0 8 1zm-2 3 2 1-1 2 2 2-1 3-2-2V7L4 6zm4-1 2 2-1 2-2-1z"/></symbol>
  </defs>
</svg>

<!-- English side -->
<section class="card card--english" aria-label="Business card, English">
  <svg class="card__shape" viewBox="0 0 800 457" preserveAspectRatio="none" aria-hidden="true">
    <rect width="800" height="457" fill="var(--brand-blue)"/>
    <path d="M522 0 L340 192 Q312 228 340 264 L534 457" fill="none" stroke="var(--edge-grey)" stroke-width="7"/>
    <path d="M532 0 L350 192 Q322 228 350 264 L546 457 L800 457 L800 0 Z" fill="var(--paper)"/>
    <circle cx="469" cy="21" r="7" fill="var(--paper)"/>
    <circle cx="469" cy="439" r="7" fill="var(--paper)"/>
  </svg>
  <div class="card__details">
    <h1 class="person__name">DANIEL HARPER</h1>
    <p class="person__role">President</p>
    <p class="address">4120 Willow Crest Road<br>Fairview, Oregon 58213</p>
    <ul class="contact-list">
      <li><svg><use href="#icon-phone"/></svg>555-318-2046</li>
      <li><svg><use href="#icon-mobile"/></svg>555-740-6129</li>
      <li><svg><use href="#icon-fax"/></svg>555-492-8731</li>
      <li><svg><use href="#icon-mail"/></svg>hello@novalinesystems.com</li>
      <li><svg><use href="#icon-globe"/></svg>www.novalinesystems.com</li>
    </ul>
  </div>
  <div class="brand">
    <span class="brand__dot"></span>
    <span class="brand__name">NOVALINE SYSTEMS</span>
  </div>
</section>

<!-- Arabic side -->
<section class="card card--arabic" aria-label="Business card, Arabic">
  <svg class="card__shape" viewBox="0 0 800 457" preserveAspectRatio="none" aria-hidden="true">
    <rect width="800" height="457" fill="var(--brand-blue)"/>
    <path d="M499 0 L313 192 Q285 228 313 264 L509 457" fill="none" stroke="var(--edge-grey)" stroke-width="7"/>
    <path d="M509 0 L323 192 Q295 228 323 264 L521 457 L800 457 L800 0 Z" fill="var(--paper)"/>
    <circle cx="442" cy="21" r="7" fill="var(--paper)"/>
    <circle cx="442" cy="439" r="7" fill="var(--paper)"/>
  </svg>
  <div class="card__details">
    <h2 class="person__name arabic" lang="ar">دانيال هاربر</h2>
    <p class="person__role arabic" lang="ar">رئيس</p>
    <p class="address arabic" lang="ar">4120 طريق ويلو كريست<br>فيرفيو ، أوريغون 58213</p>
    <ul class="contact-list">
      <li><svg><use href="#icon-phone"/></svg>555-318-2046</li>
      <li><svg><use href="#icon-mobile"/></svg>555-740-6129</li>
      <li><svg><use href="#icon-fax"/></svg>555-492-8731</li>
      <li><svg><use href="#icon-mail"/></svg>hello@novalinesystems.com</li>
      <li><svg><use href="#icon-globe"/></svg>www.novalinesystems.com</li>
    </ul>
  </div>
  <div class="brand">
    <span class="brand__dot"></span>
    <span class="brand__name">NOVALINE SYSTEMS</span>
  </div>
</section>

</body>
</html>
```